Constant Contact email marketing template

I need engaging customizable templates that can be used in multiple fundraising campaigns.

I included a school bus project that we used in a previous campaign. This campaign, however, is a $25 for $25 promotion. Consumers make a $25 contribution for the school or charity and receive back a $25 e-gift card to be used at area restaurants.

Important! This is a completely generic piece, capable of being used in schools, churches, or other civic organizations.

The 5 part example is NOT what I am looking for. I included it to suggest the concept. I am looking forward to viewing YOUR designs,

Target Market(s)

schools, leagues, nonprofit organizations

Font styles to use
Sans Serif

Colors

Designer to choose colors to be used in the design.

Requirements
Must have
• Must clearly present itself as a fundraising tool for schools, leagues and Nonprofit organizations.
• Must have 2 clickable buttons that allow member to click

```html
<!DOCTYPE html>
<html lang="en">
<head>
<meta charset="utf-8">
<title>$25 for $25 Fundraiser</title>
<link href="https://fonts.googleapis.com/css2?family=Oswald:wght@300;400;600&family=Source+Sans+3:wght@600;700;800&family=PT+Sans+Narrow&family=Kaushan+Script&family=Open+Sans:wght@400;600&display=block" rel="stylesheet">
<style>
  :root{
    --ink:#111111;
    --black:#141414;
    --navy:#262a5e;
    --gold:#b8a04a;
    --gold-light:#e3b04b;
    --red:#c8323a;
    --red-dark:#a8262e;
    --wine:#a7282f;
    --white:#ffffff;
    --silver:#d9d9d9;
  }
  *{box-sizing:border-box;margin:0;padding:0}
  html,body{width:1200px;height:2362px;overflow:hidden;background:var(--white)}
  .flyer{position:relative;width:1200px;height:2362px;overflow:hidden;background:var(--white);font-family:"Source Sans 3",Arial,sans-serif;color:var(--ink)}
  .backdrop{position:absolute;inset:0}
  .crowd-photo{position:absolute;left:0;top:0;width:920px;height:720px;
    background:radial-gradient(ellipse at 45% 35%,#c89a7c 0%,#a9b1bd 45%,rgba(230,232,236,.6) 75%,rgba(255,255,255,0) 100%);
    clip-path:path("M0 0 L900 0 C930 200 880 380 640 470 C420 550 180 600 0 720 Z");}
  .tagline{position:absolute;right:62px;top:18px;text-align:right;color:var(--white);transform:rotate(-4deg);transform-origin:right top}
  .tagline .small-script{font-family:"Kaushan Script",cursive;font-size:50px;line-height:1.1;margin-right:40px}
  .tagline .caps{font-family:"Oswald",sans-serif;font-weight:400;font-size:34px;letter-spacing:12px;color:var(--gold-light);margin-top:0;margin-right:-12px}
  .tagline .big-script{font-family:"Kaushan Script",cursive;font-size:104px;line-height:1;margin-right:0}

  .offer-frame{position:absolute;left:272px;top:612px;width:632px;height:446px;border:4px solid var(--gold-light);border-radius:22px;transform:rotate(-4deg)}
  .ticket{position:absolute;display:flex;box-shadow:0 10px 22px rgba(0,0,0,.28);background:linear-gradient(180deg,#ffffff,#eeeeee)}
  .ticket-donate{left:118px;top:580px;width:700px;height:240px;transform:rotate(-5deg)}
  .ticket-gift{left:508px;top:900px;width:620px;height:262px;transform:rotate(-6deg)}
  .ticket .face{flex:1;display:flex;align-items:center;justify-content:center}
  .ticket .price{position:relative;width:46%;display:flex;align-items:center;justify-content:center;color:var(--white);
    background:linear-gradient(135deg,var(--red) 0%,var(--red-dark) 60%,#b72c33 100%);
    clip-path:polygon(22% 0,100% 0,100% 100%,0 100%);padding-left:40px;
    font-family:"Oswald",sans-serif;font-weight:600;font-size:150px;line-height:1}
  .ticket .price sup{font-size:60px;align-self:flex-start;margin-top:28px;margin-right:4px}
  .donate-word{font-family:"Kaushan Script",cursive;font-size:112px;color:var(--wine);margin-left:60px;margin-top:20px}
  .gift-badge{border:3px solid var(--ink);padding:10px 34px 4px;text-align:center;margin-left:30px}
  .gift-badge .script{font-family:"Kaushan Script",cursive;font-size:70px;color:var(--wine);line-height:1}
  .gift-badge .label{display:inline-block;background:var(--white);font-family:"Oswald",sans-serif;font-weight:600;font-size:22px;letter-spacing:6px;color:var(--wine);margin-bottom:-18px;padding:0 10px}
  .you-get{position:absolute;left:300px;top:760px;font-family:"Kaushan Script",cursive;font-size:120px;color:var(--gold-light);transform:rotate(-6deg);text-shadow:0 4px 8px rgba(0,0,0,.15)}

  .cta-button{position:absolute;display:flex;align-items:center;justify-content:center;border-radius:50%;text-decoration:none;
    background:radial-gradient(circle at 50% 30%,#ffffff,var(--silver) 70%,#b4b4b4);box-shadow:0 8px 18px rgba(0,0,0,.25)}
  .cta-button .core{border-radius:50%;display:flex;flex-direction:column;align-items:center;justify-content:center;text-align:center;color:var(--white);font-family:"Oswald",sans-serif;font-weight:300;line-height:1.15}
  .cta-donate{left:48px;top:1205px;width:384px;height:384px}
  .cta-donate .core{width:324px;height:324px;background:radial-gradient(circle at 50% 25%,#e2633c,var(--red) 55%,#a3232a)}
  .cta-donate .lead{font-size:38px}
  .cta-donate .main{font-size:80px;line-height:1.05}
  .cta-behalf{left:62px;top:1855px;width:360px;height:360px}
  .cta-behalf .core{width:304px;height:304px;background:radial-gradient(circle at 50% 25%,#f2c24a,#d99a1b 65%,#b87a12);color:#fff6df}
  .cta-behalf .lead{font-size:36px;margin-bottom:10px}
  .cta-behalf .main{font-size:38px}

  .pitch{position:absolute;left:480px;top:1285px;width:690px}
  .pitch h2{font-weight:800;font-size:52px;line-height:1.14;color:var(--black);white-space:nowrap}
  .pitch .note{font-family:"Open Sans",sans-serif;font-size:23px;letter-spacing:2.5px;line-height:1.15;margin-top:22px;text-transform:uppercase;white-space:nowrap}
  .benefits{position:absolute;left:186px;top:1650px;list-style:none}
  .benefits li{display:flex;align-items:center;gap:16px;font-weight:700;font-size:32px;color:var(--red);line-height:1.65}
  .benefits svg{width:36px;height:36px}

  .promo{position:absolute;left:452px;top:1880px;width:548px}
  .promo h3{font-family:"Source Sans 3",sans-serif;font-weight:700;font-size:62px;color:var(--red);line-height:1}
  .promo p{font-family:"PT Sans Narrow",sans-serif;font-size:20.5px;line-height:1.4;margin-top:24px;text-align:justify;color:var(--ink)}

  .contact{position:absolute;right:40px;top:2168px;list-style:none;color:var(--white);font-family:"Open Sans",sans-serif;font-size:19px}
  .contact li{display:flex;align-items:center;justify-content:flex-end;gap:18px;height:46px;margin-bottom:14px}
  .contact .icon{width:44px;height:44px;border:2.5px solid var(--white);border-radius:50%;display:flex;align-items:center;justify-content:center}
  .contact .icon svg{width:24px;height:24px}
</style>
</head>
<body>
<main class="flyer">
  <svg class="backdrop" viewBox="0 0 1200 2362" width="1200" height="2362" aria-hidden="true">
    <defs>
      <linearGradient id="bandTop" x1="0" y1="1" x2="1" y2="0">
        <stop offset="0" stop-color="#262a5e"/><stop offset=".55" stop-color="#5c5a5a"/><stop offset="1" stop-color="#b8a04a"/>
      </linearGradient>
      <linearGradient id="bandBottom" x1="0" y1="0" x2="1" y2="0">
        <stop offset="0" stop-color="#b8a04a"/><stop offset=".5" stop-color="#6a6456"/><stop offset="1" stop-color="#262a5e"/>
      </linearGradient>
      <linearGradient id="navyCorner" x1="0" y1="0" x2="1" y2="0">
        <stop offset="0" stop-color="#262a5e"/><stop offset=".6" stop-color="#3a3c66"/><stop offset="1" stop-color="#6e6a52"/>
      </linearGradient>
    </defs>
    <path d="M0 560 C300 470 720 420 1200 260 L1200 480 C900 430 420 470 40 740 C20 700 8 640 0 610 Z" fill="url(#bandTop)"/>
    <path d="M200 560 C520 470 880 430 1200 330 L1200 420 C900 400 560 440 230 580 Z" fill="#ffffff"/>
    <path d="M560 0 L1200 0 L1200 300 C1000 390 760 410 470 460 C640 360 700 200 560 0 Z" fill="var(--black)"/>
    <path d="M0 2362 L0 2210 C260 2330 700 2260 1020 2080 C1100 2030 1160 1960 1200 1900 L1200 2362 Z" fill="url(#bandBottom)"/>
    <path d="M90 2362 C420 2340 820 2220 1200 1990 L1200 2362 Z" fill="url(#navyCorner)"/>
    <path d="M0 2362 L0 2240 C300 2360 620 2330 900 2230 C600 2360 320 2362 120 2362 Z" fill="#ffffff"/>
  </svg>

  <div class="crowd-photo" role="img" aria-label="Photo of a cheerful group of supporters celebrating with raised arms"></div>

  <div class="tagline">
    <div class="small-script">greatest</div>
    <div class="caps">FUNDRAISER</div>
    <div class="big-script">ever!</div>
  </div>

  <div class="offer-frame"></div>
  <div class="ticket ticket-donate">
    <div class="face"><span class="donate-word">donate</span></div>
    <div class="price"><sup>$</sup>25</div>
  </div>
  <div class="you-get">and you get</div>
  <div class="ticket ticket-gift">
    <div class="face">
      <div class="gift-badge"><div class="script">e-Gift</div><span class="label">CARD</span></div>
    </div>
    <div class="price"><sup>$</sup>25</div>
  </div>

  <a class="cta-button cta-donate" href="#donate">
    <span class="core"><span class="lead">CLIK HERE</span><span class="main">DONATE<br>NOW!</span></span>
  </a>
  <section class="pitch">
    <h2>Simply donate $25 and<br>we give you $25 back in<br>e-Gift Cards for<br>restaurants in your area!</h2>
    <p class="note">"Sed ut perspiciatis unde omnis iste<br>natus error sit voluptatem ac</p>
  </section>

  <ul class="benefits">
    <li><svg viewBox="0 0 24 24"><path d="M2 12 L9 20 L23 2 L9 14 Z" fill="var(--red)"/></svg>More than 500,000 deals available every day</li>
    <li><svg viewBox="0 0 24 24"><path d="M2 12 L9 20 L23 2 L9 14 Z" fill="var(--red)"/></svg>Local independent neughborhood restaurants</li>
    <li><svg viewBox="0 0 24 24"><path d="M2 12 L9 20 L23 2 L9 14 Z" fill="var(--red)"/></svg>Always available. Never expire.</li>
  </ul>

  <a class="cta-button cta-behalf" href="#donate-behalf">
    <span class="core"><span class="lead">CLIK HERE</span><span class="main">DONATE ON BEHALF<br>OF A LOVED ONE<br>OR FRIEND</span></span>
  </a>
  <section class="promo">
    <h3>$25 for $25</h3>
    <p>"Sed ut perspiciatis unde omnis iste natus error sit voluptatem accusantium doloremque laudantium, totam rem aperiam, eaque ipsa quae ab illo inventore veritatis et quasi architecto beatae vitae dicta sunt explicabo. Nemo enim ipsam voluptatem quia voluptas sit aspernatur aut odit aut fugit, sed quia consequuntur magni dolores eos qui ratione voluptatem sequi nesciunt.</p>
  </section>

  <ul class="contact">
    <li>ADDRES<span class="icon"><svg viewBox="0 0 24 24"><path d="M3 12 L12 4 L21 12 M6 10 V20 H18 V10" fill="none" stroke="#fff" stroke-width="2.2"/></svg></span></li>
    <li>+01 555 014 2837<span class="icon"><svg viewBox="0 0 24 24"><path d="M6 3 L9 3 L10.5 8 L8.5 9.5 C9.5 12 12 14.5 14.5 15.5 L16 13.5 L21 15 L21 18 C21 19.5 19.5 21 18 21 C10 20 4 14 3 6 C3 4.5 4.5 3 6 3 Z" fill="#fff"/></svg></span></li>
    <li>HELLO@GIVEFUND.ORG<span class="icon"><svg viewBox="0 0 24 24"><rect x="3" y="6" width="18" height="12" fill="#fff"/><path d="M3 6 L12 13 L21 6" fill="none" stroke="#4a4a6a" stroke-width="1.6"/></svg></span></li>
  </ul>
</main>
</body>
</html>
```